BRISKEL Need a luxury modern business card designed.

Need a luxury modern business card designed. refer to the uploaded files for the company name and logo in the zip file under source files. i will making my descion on monday. so please send in before then so if we need to edit we will have the time. we have a trade show coming up and im on a deadline for printer.

Target Market(s)

high end clients

Contact Information for Business Card

Company nAme and logo. Tobias Fennick Co-Founder / Project Manager Office # 555-318-7094 Cell # 555-642-1586 BRISKEL.CA Tobias@briskel-example.ca

Font styles to use
Other font styles liked:
• Modern

Requirements
Must have
• Company name and logo, contact info, using the black, gold and white color scheme.

```html
<!DOCTYPE html>
<html lang="en">
<head>
<meta charset="utf-8">
<title>BRISKEL Business Card</title>
<link href="https://fonts.googleapis.com/css2?family=Arimo:wght@400&display=swap" rel="stylesheet">
<style>
  :root {
    --stage: #2a2a2a;
    --card-dark: #2f2f2f;
    --card-light: #ffffff;
    --gold: #a89a65;
    --ink: #1e1e1e;
    --rule: #555555;
  }
  * { margin: 0; padding: 0; box-sizing: border-box; }
  html, body {
    width: 1200px; height: 895px; overflow: hidden;
    background: var(--stage);
    font-family: "Arimo", Arial, sans-serif;
  }
  .canvas { position: relative; width: 1200px; height: 895px; }
  .card {
    position: absolute; width: 540px; height: 309px;
    box-shadow: 0 10px 24px rgba(0,0,0,0.45);
  }
  .card--back { left: 60px; top: 120px; background: var(--card-dark); }
  .card--front {
    left: 600px; top: 466px; background: var(--card-light);
    border-bottom: 4px solid var(--gold);
  }
  .back-wordmark {
    position: absolute; left: 0; right: 0; top: 50%;
    transform: translateY(-50%);
    display: flex; align-items: center; justify-content: center; gap: 14px;
  }
  .wordmark-square { width: 18px; height: 18px; background: var(--gold); }
  .wordmark-text { font-size: 40px; letter-spacing: 8px; font-weight: 400; line-height: 1; }
  .back-wordmark .wordmark-text { color: var(--gold); }
  .front-brand {
    position: absolute; left: 0; top: 0; width: 300px; height: 100%;
    display: flex; align-items: center; justify-content: center; gap: 12px;
  }
  .front-brand .wordmark-text { color: var(--ink); font-size: 34px; letter-spacing: 6px; }
  .front-brand .wordmark-square { width: 14px; height: 14px; }
  .divider {
    position: absolute; left: 304px; top: 52px; width: 1px; height: 205px;
    background: var(--rule);
  }
  .contact { position: absolute; left: 326px; top: 56px; color: var(--ink); }
  .person-name { font-size: 20px; letter-spacing: 1px; line-height: 1; }
  .person-name .surname { color: var(--gold); }
  .person-title { font-size: 12.5px; margin-top: 4px; }
  .address { font-size: 12px; line-height: 1.3; margin-top: 18px; }
  .contact-list { list-style: none; margin-top: 18px; font-size: 12px; }
  .contact-list li { display: flex; align-items: center; gap: 10px; height: 18px; }
  .contact-list svg { width: 11px; height: 11px; flex: none; }
  .contact-label { color: var(--gold); }
</style>
</head>
<body>
<main class="canvas">
  <section class="card card--back" aria-label="Card back">
    <div class="back-wordmark">
      <span class="wordmark-square"></span>
      <span class="wordmark-text">BRISKEL</span>
    </div>
  </section>

  <section class="card card--front" aria-label="Card front">
    <div class="front-brand">
      <span class="wordmark-square"></span>
      <span class="wordmark-text">BRISKEL</span>
    </div>
    <div class="divider"></div>
    <div class="contact">
      <p class="person-name">TOBIAS <span class="surname">FENNICK</span></p>
      <p class="person-title">Co-Founder / Project Manager</p>
      <p class="address">48 Alder Lane. Unit 7<br>Fenwick, ON. A1B 2C3</p>
      <ul class="contact-list">
        <li>
          <svg viewBox="0 0 12 12" aria-hidden="true"><path d="M2.5 1 L4.5 1 L5 3.5 L3.8 4.4 Q5 7 7.6 8.2 L8.5 7 L11 7.5 L11 9.5 Q10.5 11 9 11 Q1 10 1 2.5 Q1 1 2.5 1 Z" fill="var(--gold)"/></svg>
          <span><span class="contact-label">O</span> 555-318-7094</span>
        </li>
        <li>
          <svg viewBox="0 0 12 12" aria-hidden="true"><path d="M2.5 1 L4.5 1 L5 3.5 L3.8 4.4 Q5 7 7.6 8.2 L8.5 7 L11 7.5 L11 9.5 Q10.5 11 9 11 Q1 10 1 2.5 Q1 1 2.5 1 Z" fill="var(--gold)"/></svg>
          <span><span class="contact-label">C</span> 555-642-1586</span>
        </li>
        <li>
          <svg viewBox="0 0 12 12" aria-hidden="true"><rect x="1" y="2.5" width="10" height="7" fill="none" stroke="var(--gold)" stroke-width="1.2"/><path d="M1 2.5 L6 6.5 L11 2.5" fill="none" stroke="var(--gold)" stroke-width="1.2"/></svg>
          <span>Tobias@briskel-example.ca</span>
        </li>
        <li>
          <svg viewBox="0 0 12 12" aria-hidden="true"><circle cx="6" cy="6" r="5" fill="none" stroke="var(--gold)" stroke-width="1.1"/><ellipse cx="6" cy="6" rx="2.2" ry="5" fill="none" stroke="var(--gold)" stroke-width="1"/><path d="M1 6 H11 M2 3.5 H10 M2 8.5 H10" stroke="var(--gold)" stroke-width="0.9"/></svg>
          <span>BRISKEL.CA</span>
        </li>
      </ul>
    </div>
  </section>
</main>
</body>
</html>
```